Heron Property Inspection business card

I am the principal inspector of Heron Property Inspections. I serve Northern Virginia from Winchester to Arlington.Associate, Federated Guild of Dwelling Examiners (FGDE)Graduate, FGDE Home Inspectors CourseNational Association of Home Inspectors ExamI'd like the business card to look more professional than comical.I pulled the attached picture off the web. I'd like to have something like that or an image of a house as my logo on the cards.

Target Market(s)

Persons who recently purchased a home.

Industry/Entity Type

Business

Contact Information for Business Card

Bob AllenBadger Home Inspections, LLC.4455 River RoadBluemont, Virginia 20135cell: 703-231-6680e-mail: tkmarlow@postvale.net

Font styles to use
Serif
Sans Serif

Requirements
Must have
• I'd like to have a logo, something that identifies me as a home inspector. The attached images are something that I'd like to have incorporated into my business card logo.
Nice to have
• I'd like a sketch of a house and/or a magnifying glass showing a house being inspected. The attached images are used as a suggestion only, I do not own the images.
Should not have
• Gimmicky stuff. I want to appear professional and trustworthy.

```html
<!DOCTYPE html>
<html lang="en">
<head>
<meta charset="utf-8">
<title>Heron Property Inspections — Business Card</title>
<link rel="stylesheet" href="https://fonts.googleapis.com/css2?family=Source+Sans+3:wght@400;600&display=swap">
<style>
  :root {
    --backdrop: #e8e5e1;
    --card-white: #fbfbfb;
    --brand-red: #c0161d;
    --brand-red-deep: #960f14;
    --ink: #3a3a3a;
    --divider: #555555;
    --on-red: #ffffff;
  }
  * { box-sizing: border-box; margin: 0; padding: 0; }
  html, body {
    width: 1200px; height: 818px; overflow: hidden;
    background: var(--backdrop);
    font-family: "Source Sans 3", "Helvetica Neue", Arial, sans-serif;
  }
  .business-card {
    position: absolute; left: 150px; top: 152px;
    width: 900px; height: 514px;
    background: var(--card-white);
    box-shadow: 0 10px 30px rgba(0,0,0,.18);
    overflow: hidden;
  }
  .card-panels { position: absolute; inset: 0; }
  .brand-block {
    position: absolute; left: 60px; top: 205px; width: 320px;
    display: flex; align-items: center; gap: 16px;
  }
  .brand-mark {
    width: 18px; height: 18px; flex: none;
    background: var(--brand-red);
  }
  .brand-name {
    color: var(--ink); font-weight: 600; font-size: 28px; line-height: 1.2;
  }
  .contact-side {
    position: absolute; right: 36px; top: 0; bottom: 0; width: 380px;
    color: var(--on-red);
  }
  .employee-name {
    position: absolute; right: 70px; top: 78px;
    font-size: 40px; font-weight: 600; letter-spacing: .3px; white-space: nowrap;
  }
  .employee-title {
    position: absolute; right: 70px; top: 128px;
    font-size: 21px; font-weight: 400; white-space: nowrap;
  }
  .contact-list {
    position: absolute; right: 0; bottom: 120px;
    list-style: none; text-align: right;
  }
  .contact-item {
    display: flex; justify-content: flex-end; align-items: center; gap: 14px;
    font-size: 19px; line-height: 38px; white-space: nowrap;
  }
  .contact-icon { width: 20px; height: 20px; flex: none; }
</style>
</head>
<body>
  <main class="business-card" aria-label="Heron Property Inspections business card">
    <svg class="card-panels" width="900" height="514" viewBox="0 0 900 514" aria-hidden="true">
      <defs>
        <linearGradient id="redPanel" x1="0" y1="0" x2="1" y2="1">
          <stop offset="0" style="stop-color:#c8181f"/>
          <stop offset="1" style="stop-color:#960f14"/>
        </linearGradient>
      </defs>
      <polygon points="420,0 900,0 900,514 500,514" fill="url(#redPanel)"/>
      <line x1="405" y1="0" x2="485" y2="514" stroke="#555555" stroke-width="1.5"/>
    </svg>

    <div class="brand-block">
      <span class="brand-mark"></span>
      <p class="brand-name">Tim Marlow<br>Heron Property Inspections, LLC</p>
    </div>

    <section class="contact-side">
      <h1 class="employee-name">Employee Name</h1>
      <p class="employee-title">Managing Director</p>
      <ul class="contact-list">
        <li class="contact-item">703-555-0192
          <svg class="contact-icon" viewBox="0 0 22 22" aria-label="phone"><rect x="6" y="2" width="10" height="18" rx="2" fill="none" stroke="#fff" stroke-width="2"/><circle cx="11" cy="16.5" r="1.2" fill="#fff"/></svg>
        </li>
        <li class="contact-item">tkmarlow@postvale.net
          <svg class="contact-icon" viewBox="0 0 22 22" aria-label="email"><rect x="2" y="5" width="18" height="12" fill="none" stroke="#fff" stroke-width="2"/><path d="M2 5l9 7 9-7" fill="none" stroke="#fff" stroke-width="2"/></svg>
        </li>
        <li class="contact-item">7182 Quarry Lane Fernhill, Virginia 20148
          <svg class="contact-icon" viewBox="0 0 22 22" aria-label="location"><path d="M11 2a6 6 0 0 0-6 6c0 5 6 12 6 12s6-7 6-12a6 6 0 0 0-6-6z" fill="none" stroke="#fff" stroke-width="2"/><circle cx="11" cy="8" r="2" fill="#fff"/></svg>
        </li>
      </ul>
    </section>
  </main>
</body>
</html>
```